Flyer, poster, banner and social media titles designs for Community Mending Chartre

The Harbourline Charter for Community Mending provide a nationally agreed framework to guide recovery policy and practice across Australia. The Principles support recovery practitioners, governments, non-government organisations and communities to deliver effective, community-centred recovery outcomes.
The Principles have recently been refreshed through extensive consultation and we require a contemporary visual identity and design suite that will increase awareness, engagement and practical application of the Principles.
The redesign will cover:
• A4 Brochure (primary publication)
• A3 Poster
• Pull up banner
• Social Media Tiles
The new design should:
• Create a recognisable brand for the Harbourline Charter.
• Appeal to both experienced and emerging recovery practitioners.
• Reflect contemporary disaster recovery practice.
• Feel people-focused rather than government-focused.
• Support future resources such as videos, implementation guides, presentations and workshop materials.
• Remain relevant for several years without requiring a major redesign.
Target Audience
• Disaster recovery practitioners
• Government agencies
• Non-government organisations
• Community recovery workers
• Recovery managers and leaders
• Community stakeholders and volunteers
The visual identity should reflect the six Principles:
• Understanding Context
• Recognising Complexity
• Community-Centred Approaches
• Coordination
• Communication
• Capacity Building
The design should communicate:
• Recovery is centred on people and communities.
• Recovery is collaborative and involves many sectors.
• Recovery is adaptive, inclusive and evidence-informed.
• Recovery supports resilience and long-term wellbeing.
• The Principles provide practical guidance for recovery practice.
We are looking for:
• Modern and professional
• Warm and approachable
• Human-centred
• Inclusive and accessible
• Australian in context
• Visually engaging
• Suitable for print and digital use
We would like to avoid:
• Images of disaster destruction
• Emergency response imagery (fire trucks, flashing lights, etc.)
• Overly corporate or bureaucratic designs
• Designs that focus on deficits rather than recovery and growth
Consider themes such as:
• Connection and collaboration
• Communities and people
• Growth, recovery and renewal
Accessibility
Designs should:
• Meet accessibility best practice
• Use clear typography
• Achieve strong colour contrast
• Be suitable for both digital and print formats

Deliverables
1. Principles Brochure
• A4 trifold size x 2 (online and print friendly version)
• A side to include cover side, logos side and overview of principles.
• B side full details of the principles
• Graphic to highlight the 3 c’s concept (RECOVERY Context, complexity, community centred, coordinate, communicate and capacity). Currently 3 circles.
• Can be printed and distributed electronically
2. Poster
• A1 and A3 versions
• Suitable for office and workshop display
3. Pull-Up Banner - 850 mm (W) × 2000 mm (H)
• Conference and event use
• High visual impact
• Strong branding and concise messaging
4. Social Media Tiles x 3

We are providing an extension and increasing the budget following feedback from designers. We are wanting the resources to look and feel different from the existing designs, considering either a different colour palette in the designs or different motif with the leave design. Any nature based designs should consider the Australian fauna or flora. Also suggest avoiding images in the designs. The principles are not numbered or liner in the concept of how they function. Happy to answer any further questions and thank you for your suggested concepts.

Disaster recovery practitioners, Government agencies , Non-government organisations, Community recovery workers and Community stakeholders and volunteers

Disaster recovery

• Modern, warm, visually engaging, human-centred, Australian in context and different to the current design.
• Symbols for each principles
• Images of disaster destruction, Emergency response imagery, Overly corporate or bureaucratic designs, Designs that focus on deficits rather than recovery and growth, avoid too much black

```html
<!DOCTYPE html>
<html lang="en">
<head>
<meta charset="utf-8">
<title>Harbourline Charter for Community Mending – Brochure</title>
<link href="https://fonts.googleapis.com/css2?family=Lora:wght@400;500;600&family=Lato:wght@400;700&display=swap" rel="stylesheet">
<style>
:root{
  --backdrop:#808080;
  --cream:#fbf9f4;
  --sand:#f5ede3;
  --forest:#0b4038;
  --ink:#2b2b2b;
  --heading-green:#2f5e4c;
  --context:#3f7d5a;
  --community:#d9622b;
  --communicate:#e0a12a;
  --complexity:#6a8f3c;
  --coordinate:#3c6f8a;
  --capacity:#cc5a2a;
  --lime:#7aa33a;
  --gold:#e6b04a;
  --ring-context:#4a5a45;
  --ring-capacity:#b8b27a;
  --ring-complexity:#dba23a;
  --ring-communicate:#cf5a3c;
  --ring-coordinate:#b8553a;
  --ring-community:#d9a08a;
  --serif:'Lora',Georgia,serif;
  --sans:'Lato',Arial,sans-serif;
}
*{box-sizing:border-box;margin:0;padding:0}
html,body{width:764px;height:1200px;overflow:hidden}
body{background:var(--backdrop);position:relative;font-family:var(--sans);color:var(--ink)}
.side{position:absolute;left:17px;width:727px;height:560px;display:flex}
.side--outer{top:18px}
.side--inner{top:601px;left:16px;height:562px}
.panel{position:relative;width:242px;height:100%;overflow:hidden}
.panel--cream{background:var(--cream)}
.panel--sand{background:var(--sand)}
.panel--forest{background:var(--forest);color:#fff}

.sprig{position:absolute;border-radius:50%;}
.sprig--green{background:radial-gradient(ellipse at center,rgba(86,122,84,.55),rgba(86,122,84,0) 70%)}
.sprig--faint{background:radial-gradient(ellipse at center,rgba(150,180,150,.25),rgba(150,180,150,0) 70%)}
.sprig--gold{background:radial-gradient(ellipse at center,rgba(200,160,80,.35),rgba(200,160,80,0) 70%)}

/* intro panel */
.intro{padding:26px 16px 0 17px}
.intro__title{font-family:var(--serif);font-weight:400;font-size:15.5px;line-height:22px;color:var(--heading-green)}
.intro__text{font-size:8.2px;line-height:15.6px;margin-top:10px;color:#333}
.intro__text + .intro__text{margin-top:10px}
.intro__sub{font-family:var(--serif);font-weight:400;font-size:15.5px;color:var(--heading-green);margin-top:14px}
.cycle{position:absolute;left:0;top:0;width:242px;height:560px}
.cycle text{font-family:var(--sans);font-size:8.4px;fill:#2b2b2b;text-anchor:middle}

/* partners panel */
.partners{position:absolute;left:18px;top:113px;width:210px;height:418px;background:#fff;border-radius:10px;padding:18px 12px;display:grid;grid-template-columns:1fr 1fr;grid-auto-rows:1fr;gap:6px 8px}
.partner{display:flex;flex-direction:column;align-items:center;justify-content:center;gap:4px;text-align:center;font-family:var(--sans);font-weight:700;font-size:7px;line-height:9px;color:var(--forest)}
.partner__dot{width:20px;height:20px;border-radius:50%;background:#e2e8e2}
.partner--wide{grid-column:1 / span 2;flex-direction:row;justify-content:flex-start;padding-left:4px}

/* cover panel */
.cover__eyebrow{position:absolute;left:18px;top:68px;font-size:8.6px;letter-spacing:.3px;color:#fff}
.cover__mark{position:absolute;left:17px;top:79px;font-family:var(--serif);font-weight:600;font-size:29px;line-height:28px}
.cover__mark span{display:block}
.cover__mark .accent{color:var(--lime);font-size:27px;font-weight:500}
.cover__title{position:absolute;left:17px;top:172px;font-family:var(--serif);font-weight:400;font-size:30px;line-height:34.5px;color:#fff}
.cover__tagline{position:absolute;left:18px;top:334px;font-family:var(--serif);font-size:13.6px;line-height:19px;color:var(--gold)}

/* principle panels */
.inner-col{position:relative;width:245px;height:100%;display:flex;flex-direction:column}
.principle{position:relative;height:270px;padding:26px 14px 0 16px}
.principle + .principle{border-top:1px solid #e6e0d6;height:292px}
.principle__head{display:flex;gap:9px;align-items:flex-start}
.principle__icon{flex:0 0 34px;height:34px;border-radius:50%;display:flex;align-items:center;justify-content:center}
.principle__title{font-family:var(--serif);font-weight:400;font-size:16px;line-height:21.5px}
.principle__lead{font-size:8.2px;line-height:13.8px;margin-top:13px;color:#333}
.principle__list{list-style:none;margin-top:12px}
.principle__list li{position:relative;padding-left:17px;font-size:8.2px;line-height:13.8px;margin-bottom:10px;color:#333}
.principle__list li::before{content:"";position:absolute;left:4px;top:5px;width:4.5px;height:4.5px;border-radius:50%;background:var(--dot)}
.t-context{color:var(--context)} .bg-context{background:var(--context)}
.t-community{color:var(--community)} .bg-community{background:var(--community)}
.t-communicate{color:var(--communicate)} .bg-communicate{background:var(--communicate)}
.t-complexity{color:var(--complexity)} .bg-complexity{background:var(--complexity)}
.t-coordinate{color:var(--coordinate)} .bg-coordinate{background:var(--coordinate)}
.t-capacity{color:var(--capacity)} .bg-capacity{background:var(--capacity)}
</style>
</head>
<body>

<!-- Outer side: intro, partners, cover -->
<section class="side side--outer">
  <div class="panel panel--cream">
    <div class="intro">
      <h2 class="intro__title">Harbourline Charter for<br>Community Mending</h2>
      <p class="intro__text">Disasters can deeply impact lives and livelihoods. Working with communities recovering from disasters is complex and challenging. Recovery is long-term, non-linear and dynamic, particularly in the context of compounding and concurrent disasters. These principles are a way to guide our efforts, our approach, our planning and our decision-making.</p>
      <p class="intro__text">Disaster recovery is part of emergency management, which includes the broader components of prevention, preparedness and response. Planning for recovery is integral to emergency preparation, and mitigation actions are often initiated as part of recovery.</p>
      <h3 class="intro__sub">Successful Recovery</h3>
    </div>
    <div class="sprig sprig--faint" style="left:20px;top:330px;width:220px;height:230px" role="img" aria-label="Faint watercolour foliage behind the principle circles"></div>
    <div class="sprig sprig--green" style="left:-20px;top:505px;width:100px;height:80px" role="img" aria-label="Botanical sprig illustration in the corner"></div>
    <svg class="cycle" viewBox="0 0 242 560" aria-label="Six interlinked principles of successful recovery">
      <g fill="none" stroke-width="2.4">
        <circle cx="117" cy="364" r="44" stroke="var(--ring-context)"/>
        <circle cx="60" cy="404" r="43" stroke="var(--ring-capacity)"/>
        <circle cx="180" cy="404" r="43" stroke="var(--ring-complexity)"/>
        <circle cx="85" cy="480" r="43" stroke="var(--ring-coordinate)"/>
        <circle cx="158" cy="480" r="43" stroke="var(--ring-community)"/>
        <circle cx="119" cy="428" r="44" stroke="var(--cream)" stroke-width="6"/>
        <circle cx="119" cy="428" r="44" stroke="var(--ring-communicate)" stroke-width="3"/>
        <circle cx="119" cy="428" r="40" stroke="var(--ring-communicate)" stroke-width="1.2"/>
      </g>
      <text x="117" y="355">Understand the</text><text x="117" y="367">CONTEXT</text>
      <text x="48" y="389">Recognise</text><text x="48" y="401">and build</text><text x="48" y="413">CAPACITY</text>
      <text x="191" y="395">Recognise</text><text x="191" y="407">COMPLEXITY</text>
      <text x="119" y="423">COMMUNICATE</text><text x="119" y="435">effectively</text>
      <text x="79" y="483">COORDINATE</text><text x="79" y="495">all activities</text>
      <text x="164" y="467">Use</text><text x="164" y="479">COMMUNITY-</text><text x="164" y="491">CENTRED</text><text x="164" y="503">approaches</text>
    </svg>
  </div>

  <div class="panel panel--sand">
    <div class="sprig sprig--green" style="left:14px;top:2px;width:175px;height:100px" role="img" aria-label="Watercolour eucalyptus branch illustration"></div>
    <div class="partners" aria-label="Partner organisations">
      <div class="partner"><span class="partner__dot"></span>Harbourline Department of Community Services</div>
      <div class="partner"><span class="partner__dot"></span>Harbourline Department of Civic Safety</div>
      <div class="partner"><span class="partner__dot"></span>Southern Cross Relief Society</div>
      <div class="partner"><span class="partner__dot"></span>Government of Coral Bay State</div>
      <div class="partner"><span class="partner__dot"></span>Government of Westreach</div>
      <div class="partner"><span class="partner__dot"></span>Islandia Government</div>
      <div class="partner"><span class="partner__dot"></span>Sunreach Government</div>
      <div class="partner"><span class="partner__dot"></span>Capital Ridge Government</div>
      <div class="partner"><span class="partner__dot"></span>Top End Territory Government</div>
      <div class="partner"><span class="partner__dot"></span>Southvale State Government</div>
      <div class="partner partner--wide"><span class="partner__dot"></span>Eastmere Office of Emergency Management</div>
    </div>
  </div>

  <div class="panel panel--forest">
    <p class="cover__eyebrow">HARBOURLINE CHARTER FOR</p>
    <p class="cover__mark"><span>Community</span><span class="accent">Mending</span></p>
    <div class="sprig" style="left:148px;top:80px;width:80px;height:60px;background:radial-gradient(ellipse,rgba(122,163,58,.7),rgba(122,163,58,0) 70%)" role="img" aria-label="Green leaf sprig beside the wordmark"></div>
    <h1 class="cover__title">Harbourline<br>Charter for<br>Community<br>Mending</h1>
    <p class="cover__tagline">Guiding recovery. Strengthening<br>communities.</p>
    <div class="sprig sprig--gold" style="left:0;top:340px;width:260px;height:240px" role="img" aria-label="Gold line drawing of a leafy fern branch"></div>
  </div>
</section>

<!-- Inner side: principle details -->
<section class="side side--inner">
  <div class="inner-col panel--cream">
    <article class="principle">
      <div class="principle__head">
        <span class="principle__icon bg-context"><svg width="18" height="18" viewBox="0 0 18 18" fill="none" stroke="#fff" stroke-width="1.2"><circle cx="9" cy="7" r="4.5"/><path d="M7 12h4M7.5 14.5h3"/></svg></span>
        <h3 class="principle__title t-context">Understand the<br>CONTEXT:</h3>
      </div>
      <p class="principle__lead">Successful recovery is based on an understanding of the community context, with each community having its own history, values and dynamics. Recovery</p>
      <ul class="principle__list" style="--dot:var(--context)">
        <li>Acknowledge existing strengths and capacity, including past experiences and future aspirations;</li>
        <li>Appreciate the risks and stressors faced by the community;</li>
        <li>Support people who may be at greater risk or disproportionately impacted;</li>
      </ul>
    </article>
    <article class="principle">
      <div class="principle__head">
        <span class="principle__icon bg-complexity"><svg width="18" height="18" viewBox="0 0 18 18" fill="none" stroke="#fff" stroke-width="1.2"><circle cx="8" cy="8" r="5"/><circle cx="8" cy="8" r="2"/><path d="M11.5 11.5L15 15"/></svg></span>
        <h3 class="principle__title t-complexity">Recognise<br>COMPLEXITY</h3>
      </div>
      <p class="principle__lead">Successful recovery is responsive to the complex and evolving nature of disasters and their impacts on communities, including compounding, cascading and concurrent events. Recovery should recognise that:</p>
      <ul class="principle__list" style="--dot:var(--complexity)">
        <li>Disasters lead to a range of effects and impacts that require a variety of approaches; they can also leave long-term legacies;</li>
        <li>Affected individuals and the community have diverse needs, wants and expectations, which can evolve rapidly;</li>
      </ul>
      <div class="sprig sprig--green" style="left:140px;top:6px;width:70px;height:40px" role="img" aria-label="Small eucalyptus leaf sprig"></div>
      <div class="sprig sprig--green" style="left:-20px;top:230px;width:80px;height:70px" role="img" aria-label="Botanical sprig illustration in the corner"></div>
    </article>
  </div>

  <div class="inner-col panel--sand">
    <article class="principle">
      <div class="principle__head">
        <span class="principle__icon bg-community"><svg width="18" height="18" viewBox="0 0 18 18" fill="none" stroke="#fff" stroke-width="1.2"><circle cx="5" cy="7" r="2"/><circle cx="9" cy="5" r="2"/><circle cx="13" cy="7" r="2"/><path d="M2 15v-3h6v3M10 15v-3h6v3"/></svg></span>
        <h3 class="principle__title t-community">Use COMMUNITY<br>CENTRED approaches</h3>
      </div>
      <p class="principle__lead">Successful recovery is community-centred, responsive and flexible, engaging with community and supporting them to move forward, with shared responsibilities. Recovery should:</p>
      <ul class="principle__list" style="--dot:var(--community);margin-top:16px">
        <li>Assist and enable individuals, families and the community to actively participate in their own recovery;</li>
        <li>Recognise that individuals and the community may need different levels of support at various times;</li>
      </ul>
    </article>
    <article class="principle">
      <div class="principle__head">
        <span class="principle__icon bg-coordinate"><svg width="18" height="18" viewBox="0 0 18 18" fill="none" stroke="#fff" stroke-width="1.2"><circle cx="5" cy="5" r="1.8"/><circle cx="9" cy="5" r="1.8"/><circle cx="13" cy="5" r="1.8"/><path d="M3 10h12M5 10v5M9 10v5M13 10v5"/></svg></span>
        <h3 class="principle__title t-coordinate">COORDINATE all<br>activities</h3>
      </div>
      <p class="principle__lead">Successful recovery requires a planned, coordinated and adaptive approach, between community and partner agencies, based on continuing assessment of impacts and need. Recovery should:</p>
      <ul class="principle__list" style="--dot:var(--coordinate);margin-top:16px">
        <li>Have clearly articulated and shared goals based on desired outcomes;</li>
        <li>Be flexible, taking into account changes in community needs or stakeholder expectations.</li>
        <li>Be guided by those with experience and expertise, using skilled, authentic and capable community leadership;</li>
      </ul>
      <div class="sprig sprig--green" style="left:160px;top:245px;width:100px;height:60px" role="img" aria-label="Botanical branch illustration along the lower edge"></div>
    </article>
  </div>

  <div class="inner-col panel--cream" style="width:237px">
    <article class="principle">
      <div class="principle__head">
        <span class="principle__icon bg-communicate"><svg width="18" height="18" viewBox="0 0 18 18" fill="none" stroke="#fff" stroke-width="1.2"><rect x="3" y="2.5" width="12" height="7" rx="1"/><path d="M5.5 5h7M5.5 7h5"/><circle cx="5" cy="12.5" r="1.5"/><circle cx="13" cy="12.5" r="1.5"/></svg></span>
        <h3 class="principle__title t-communicate">COMMUNICATE<br>effectively</h3>
      </div>
      <p class="principle__lead">Successful recovery is built on effective communication between the affected community and other partners. Recovery should:</p>
      <ul class="principle__list" style="--dot:var(--communicate)">
        <li>Recognise that communication should be two-way, transparent and ongoing, building trust through shared understanding and feedback;</li>
        <li>Ensure that information is accessible to audiences in diverse situations, addresses a variety of communication needs, and is provided through a range of communication channels and networks;</li>
      </ul>
      <div class="sprig sprig--green" style="left:155px;top:-20px;width:100px;height:80px" role="img" aria-label="Botanical sprig illustration in the corner"></div>
    </article>
    <article class="principle">
      <div class="principle__head">
        <span class="principle__icon bg-capacity"><svg width="18" height="18" viewBox="0 0 18 18" fill="none" stroke="#fff" stroke-width="1.2"><circle cx="6" cy="6" r="2.2"/><path d="M2.5 13c0-2 1.6-3.5 3.5-3.5s3.5 1.5 3.5 3.5"/><circle cx="12.5" cy="12" r="2.5"/><path d="M13 3v3M11.5 4.5h3"/></svg></span>
        <h3 class="principle__title t-capacity">Recognise and build<br>CAPACITY</h3>
      </div>
      <p class="principle__lead">Successful recovery recognises, supports and builds on individual, community and organisational capacity and resilience. Recovery should:</p>
      <ul class="principle__list" style="--dot:var(--capacity)">
        <li>Assess capability and capacity requirements before, during and after a disaster;</li>
        <li>Support the development of self-reliance, preparation and disaster mitigation;</li>
        <li>Quickly identify and mobilise community skills, strengths and resources;</li>
      </ul>
      <div class="sprig sprig--faint" style="left:170px;top:190px;width:80px;height:110px" role="img" aria-label="Faint watercolour foliage in the corner"></div>
    </article>
  </div>
</section>

</body>
</html>
```